Business card design for Automotive workshop

We need a business card for a new automotive repair and tyre shop called Keelstone Prime Automotive located in New Zealand. We are a clean, modern and fresh workshop and company.

Front needs to feature logo,
my name:
Marlo Fenwicke (director)

Address:
48 Tarn Lane
Corrowick 3627

Phone: 07 594 2713
Mobile: 027 451 9362
Email: office@keelstoneautomotive.example.nz
Website: keelstoneautomotive.example.nz

Back needs to feature an area to write down appointment details, date and time.

Also feature a list of jobs and work we do such as,
Vehicle Servicing
All Mechanical Repairs
Warrant of Fitness
Tyres & Wheel Alignments
Automotive Diagnostics
Automotive Parts & Supplies

```html
<!DOCTYPE html>
<html lang="en">
<head>
<meta charset="utf-8">
<title>Keelstone Prime Automotive – Business Card</title>
<link rel="stylesheet" href="https://fonts.googleapis.com/css2?family=Michroma&family=Roboto:wght@400;700&display=swap">
<style>
  :root {
    --bg: #3b3b3d;
    --card: #ffffff;
    --red: #e3141f;
    --ink: #1c1c1c;
    --grey: #555555;
    --rule: #9a9a9a;
  }
  * { box-sizing: border-box; margin: 0; padding: 0; }
  html, body { width: 1200px; height: 900px; overflow: hidden; background: var(--bg); }
  .stage { position: relative; width: 1200px; height: 900px; }
  .card {
    position: absolute; left: 250px; width: 700px; height: 400px;
    background: var(--card); box-shadow: 0 10px 30px rgba(0,0,0,.45);
  }
  .card--back { top: 40px; }
  .card--front { top: 460px; }

  .brand {
    position: absolute; left: 0; right: 0; text-align: center;
    font-family: "Michroma", sans-serif; color: var(--red);
    font-size: 26px; line-height: 1.15; letter-spacing: 1px;
  }
  .brand__mark {
    display: inline-block; width: 12px; height: 12px; background: var(--red);
    margin-right: 12px; vertical-align: middle; position: relative; top: -3px;
  }
  .card--back .brand { top: 30px; }
  .card--front .brand { top: 70px; }

  /* back */
  .services { position: absolute; top: 120px; left: 0; right: 0; text-align: center; font-family: "Roboto", sans-serif; }
  .services__title { color: var(--red); font-weight: 700; font-size: 19px; letter-spacing: .5px; margin-bottom: 8px; }
  .services__list { color: var(--grey); font-size: 15px; line-height: 1.45; }
  .services__dot { color: var(--red); padding: 0 6px; }
  .appointment { position: absolute; left: 60px; right: 60px; top: 260px; font-family: "Roboto", sans-serif; font-size: 16px; }
  .appointment__row { display: flex; align-items: flex-end; gap: 8px; margin-bottom: 34px; }
  .appointment__label { color: var(--red); }
  .appointment__fill { flex: 1; border-bottom: 2px dotted #444; height: 1px; margin-bottom: 4px; }
  .appointment__fill--date { flex: 1.6; }

  /* front */
  .divider { position: absolute; left: 50px; right: 50px; top: 220px; height: 1px; background: var(--rule); }
  .divider__accent { position: absolute; left: 0; top: -2px; width: 220px; height: 4px; background: var(--red); }
  .person { position: absolute; left: 50px; top: 236px; font-family: "Michroma", sans-serif; }
  .person__name { color: var(--red); font-size: 22px; }
  .person__role { color: var(--ink); font-size: 12px; margin-top: 4px; }
  .person__address { color: var(--grey); font-size: 13px; line-height: 1.6; margin-top: 16px; }
  .contact { position: absolute; right: 50px; top: 272px; font-family: "Michroma", sans-serif; color: var(--grey); text-align: right; list-style: none; }
  .contact__item { display: flex; justify-content: flex-end; align-items: center; gap: 10px; height: 22px; }
  .contact__item--phone { font-size: 15px; }
  .contact__item--web { font-size: 11px; }
  .contact__icon { width: 13px; height: 13px; fill: var(--red); flex: none; }
</style>
</head>
<body>
<main class="stage">

  <section class="card card--back" aria-label="Card back">
    <div class="brand"><span class="brand__mark"></span>KEELSTONE PRIME<br>AUTOMOTIVE</div>
    <div class="services">
      <p class="services__title">VEHICLE SERVICING</p>
      <p class="services__list">All Mechanical Repairs<span class="services__dot">•</span>Warrant of Fitness<span class="services__dot">•</span>Tyres &amp; Wheel Alignments</p>
      <p class="services__list">Automotive Diagnostics<span class="services__dot">•</span>Automotive Parts &amp; Supplies</p>
    </div>
    <div class="appointment">
      <div class="appointment__row"><span class="appointment__label">Date:</span><span class="appointment__fill appointment__fill--date"></span><span class="appointment__label">Time:</span><span class="appointment__fill"></span></div>
      <div class="appointment__row"><span class="appointment__label">Date:</span><span class="appointment__fill appointment__fill--date"></span><span class="appointment__label">Time:</span><span class="appointment__fill"></span></div>
    </div>
  </section>

  <section class="card card--front" aria-label="Card front">
    <div class="brand"><span class="brand__mark"></span>KEELSTONE PRIME<br>AUTOMOTIVE</div>
    <div class="divider"><span class="divider__accent"></span></div>
    <div class="person">
      <p class="person__name">Marlo Fenwicke</p>
      <p class="person__role">Director</p>
      <p class="person__address">48 Tarn Lane<br>Corrowick 3627</p>
    </div>
    <ul class="contact">
      <li class="contact__item contact__item--phone">07 594 2713
        <svg class="contact__icon" viewBox="0 0 24 24"><path d="M6.6 10.8a15 15 0 0 0 6.6 6.6l2.2-2.2c.3-.3.7-.4 1-.2 1.1.4 2.3.6 3.6.6.6 0 1 .4 1 1V20c0 .6-.4 1-1 1A17 17 0 0 1 3 4c0-.6.4-1 1-1h3.5c.6 0 1 .4 1 1 0 1.3.2 2.5.6 3.6.1.3 0 .7-.2 1z"/></svg></li>
      <li class="contact__item contact__item--phone">027 451 9362
        <svg class="contact__icon" viewBox="0 0 24 24"><path d="M7 1h10a2 2 0 0 1 2 2v18a2 2 0 0 1-2 2H7a2 2 0 0 1-2-2V3a2 2 0 0 1 2-2zm0 3v14h10V4zm5 15.5a1 1 0 1 0 0 2 1 1 0 0 0 0-2z"/></svg></li>
      <li class="contact__item contact__item--web">office@keelstoneautomotive.example.nz
        <svg class="contact__icon" viewBox="0 0 24 24"><path d="M2 5h20v14H2zm2 2v.5l8 5 8-5V7zm0 2.8V17h16V9.8l-8 5z"/></svg></li>
      <li class="contact__item contact__item--web">www.keelstoneautomotive.example.nz
        <svg class="contact__icon" viewBox="0 0 24 24"><circle cx="12" cy="12" r="10"/></svg></li>
    </ul>
  </section>

</main>
</body>
</html>
```